Summit Bodyform Gym Website

We need a website design for our gym.

Summit is the UAE's first calisthenics and parkour gym. The theme under which the gym revolves is that one does not require any machinery to workout as our bodies could be themselves the machinery. The gym is designed to be the more of a social hub rather than an "in-and-out" gym, where people come train, have fun, hang out and socialize for a few hours rather than just train for 60 minutes then leave. The gym is designed to be a big open space with lots of natural sunlight, natural wood and plants all over the place to create a natural and refreshing setting. We also use recycled material throughout the gym and recycle our waste as being green is part of our philosophy. We currently also have some of the world's top and most recognized calisthenics athletes working with us.

We would like our website to reflect all that as well as provide a simple, interactive and fun way for visitors to be able to get class and gym information, check out gym media and contact us for bookings.

Target Market(s)

Ages 15-35

Industry/Entity Type

Fitness

Coding

Coded - Design and coding required

Number of Pages Required

4 page

Font styles to use
Decorative

Colors
0792cd

Requirements
Must have
• Class descriptions
• Gym description
• Class schedules
• Trainer profiles
• Gym philosophy
• Contact Details
Nice to have
• A link to contact us directly for a free first trial class

```html
<!DOCTYPE html>
<html lang="en">
<head>
<meta charset="utf-8">
<title>Summit Bodyform Gym</title>
<link rel="stylesheet" href="https://fonts.googleapis.com/css2?family=Arimo:wght@400;700&display=swap">
<style>
:root{
  --brand:#0792cd;
  --brand-dark:#0a6f93;
  --ink:#222;
  --muted:#666;
  --panel:#e7e7e7;
  --dark:#2e2e2e;
  --dark-line:#474747;
  --footer-text:#bdbdbd;
  --white:#fff;
}
*{box-sizing:border-box;margin:0;padding:0}
html,body{width:1200px;height:2302px;overflow:hidden}
body{font-family:"Arimo",Arial,sans-serif;background:var(--dark);color:var(--ink);position:relative}
.abs{position:absolute}

/* header */
.site-header{position:absolute;left:0;top:0;width:1200px;height:123px;background:var(--white)}
.brand{position:absolute;left:100px;top:30px;display:flex;align-items:center;gap:12px}
.brand-mark{width:22px;height:22px;border-radius:50%;background:var(--brand)}
.brand-name{font-size:34px;font-weight:700;color:#2a2a2a;letter-spacing:-.5px}
.main-nav{position:absolute;left:348px;top:51px;display:flex;gap:28px;font-size:11.5px;text-transform:uppercase;color:#333}
.main-nav .active{color:var(--brand)}

/* hero */
.hero{position:absolute;left:0;top:123px;width:1200px;height:580px;background:linear-gradient(180deg,#8b9298 0%,#aeb4b8 35%,#6e7378 70%,#3f4346 100%)}
.hero-caption{position:absolute;left:100px;top:184px;width:414px;height:196px;background:rgba(40,40,40,.55);padding:20px 20px}
.hero-caption h1{font-weight:400;color:var(--white);font-size:33px;line-height:41px;letter-spacing:1px;text-transform:uppercase}
.btn{display:inline-block;background:linear-gradient(180deg,#1597c4,#0a6f93);color:var(--white);text-transform:uppercase;font-size:15px;border-radius:3px;text-align:center}
.hero-caption .btn{position:absolute;left:20px;top:124px;width:158px;height:46px;line-height:46px}
.hero-arrow{position:absolute;top:248px;width:50px;height:50px}

/* content panel */
.panel{position:absolute;left:100px;top:652px;width:1000px;height:1223px;background:var(--panel)}
.section-title{position:absolute;font-size:21px;font-weight:400;text-transform:uppercase;color:#222}
.class-card{position:absolute;top:72px;width:221px;height:163px;box-shadow:0 2px 4px rgba(0,0,0,.25)}
.class-card .label{position:absolute;left:0;bottom:0;width:100%;height:49px;line-height:49px;background:rgba(30,30,30,.7);color:var(--brand);font-size:15px;text-transform:uppercase;text-align:center}
.trial-banner{position:absolute;left:27px;top:264px;width:947px;height:157px;background:linear-gradient(90deg,#8e8e8e 0%,#bfbfbf 45%,#c4c4c4 100%);box-shadow:0 2px 4px rgba(0,0,0,.25)}
.trial-banner .text{position:absolute;left:493px;top:66px;color:var(--white);font-size:18px;text-transform:uppercase}
.trial-banner .btn{position:absolute;left:777px;top:56px;width:153px;height:44px;line-height:44px}

.date-box{position:absolute;left:27px;top:493px;width:71px;height:64px;background:linear-gradient(180deg,#1597c4,#0a6f93);color:var(--white);text-align:center}
.date-box .day{display:block;font-size:22px;padding-top:8px}
.date-box .month{display:block;font-size:13px;text-transform:uppercase;margin-top:4px}
.post-card{position:absolute;left:121px;top:493px;width:579px;height:686px;background:var(--white)}
.post-image{width:579px;height:363px;background:linear-gradient(160deg,#6b4a34,#3f5a3a 50%,#2d3b6a)}
.post-body{padding:18px 32px}
.post-title{font-size:16px;font-weight:400;color:var(--brand)}
.post-date{font-size:12px;color:var(--muted);margin-top:12px}
.post-text{font-size:12.5px;line-height:23px;color:#444;margin-top:16px}
.post-card .btn{position:absolute;left:32px;top:606px;width:138px;height:43px;line-height:43px;text-transform:none;font-size:15px}

.trainer-card{position:absolute;left:729px;width:245px;height:191px;box-shadow:0 2px 4px rgba(0,0,0,.25)}
.trainer-card .info{position:absolute;left:0;bottom:0;width:100%;height:57px;background:rgba(30,30,30,.75);text-align:center;padding-top:10px}
.trainer-card .name{display:block;color:var(--brand);font-size:15px;text-transform:uppercase}
.trainer-card .role{display:block;color:var(--white);font-size:12px;margin-top:4px}

.hours{position:absolute;left:729px;top:973px;width:245px;border-collapse:collapse;font-size:12.5px}
.hours td{height:51.5px;border-bottom:1px solid #ddd}
.hours td:first-child{background:var(--white);padding-left:15px;width:145px}
.hours td:last-child{background:#d6d6d6;padding-left:15px}

/* footer */
.footer-col{position:absolute;top:1913px;width:212px;color:var(--footer-text);font-size:12px;line-height:23px}
.footer-col h3{font-size:13px;font-weight:400;color:var(--white);text-transform:uppercase;padding-bottom:10px;border-bottom:1px solid var(--dark-line);margin-bottom:25px}
.footer-col p+p{margin-top:12px}
.about-thumb{float:left;width:106px;height:86px;margin:2px 14px 4px 0;background:linear-gradient(180deg,#8a6a4a,#5a4436)}
.signup{display:flex;height:43px;margin-top:10px;margin-bottom:16px}
.signup .field{width:144px;background:var(--white);color:#999;font-size:11px;line-height:43px;padding-left:15px}
.signup .send{width:67px;background:var(--brand-dark);color:var(--white);font-size:11px;line-height:43px;text-align:center}
.footer-bottom{position:absolute;left:127px;top:2237px;width:947px;border-top:1px solid var(--dark-line);text-align:center;color:var(--footer-text);font-size:11.5px;padding-top:25px;text-transform:uppercase}
.footer-bottom span{text-transform:none}
</style>
</head>
<body>

<header class="site-header">
  <div class="brand"><span class="brand-mark"></span><span class="brand-name">Summit</span></div>
  <nav class="main-nav">
    <span class="active">Home</span><span>Class Descriptions</span><span>Gym Description</span><span>Class Schedules</span><span>Trainer Profiles</span><span>Gym Philosophy</span><span>Contact</span>
  </nav>
</header>

<section class="hero" role="img" aria-label="Open calisthenics gym floor with climbing net, rigs and two athletes training">
  <div class="hero-caption">
    <h1>Personal Training<br>at its best</h1>
    <span class="btn">Learn More</span>
  </div>
  <svg class="hero-arrow" style="left:24px" viewBox="0 0 50 50"><circle cx="25" cy="25" r="25" fill="rgba(255,255,255,.6)"/><path d="M29 14 L18 25 L29 36" stroke="#888" stroke-width="5" fill="none"/></svg>
  <svg class="hero-arrow" style="left:1112px" viewBox="0 0 50 50"><circle cx="25" cy="25" r="25" fill="rgba(255,255,255,.6)"/><path d="M21 14 L32 25 L21 36" stroke="#888" stroke-width="5" fill="none"/></svg>
</section>

<main class="panel">
  <h2 class="section-title" style="left:27px;top:28px">Popular Classes</h2>
  <div class="class-card" style="left:27px;background:linear-gradient(135deg,#e9e4df,#b7a898)" role="img" aria-label="Weight training class photo"><span class="label">Weight Training</span></div>
  <div class="class-card" style="left:270px;background:linear-gradient(135deg,#eceae6,#a9a39c)" role="img" aria-label="Personal training session photo"><span class="label">Personal Training</span></div>
  <div class="class-card" style="left:512px;background:linear-gradient(135deg,#8fc3d8,#d4a7b4)" role="img" aria-label="Group training class photo"><span class="label">Group Training</span></div>
  <div class="class-card" style="left:753px;background:linear-gradient(135deg,#d9e6ea,#8aa7b5)" role="img" aria-label="Yoga class photo"><span class="label">Yoga Classes</span></div>

  <div class="trial-banner" role="img" aria-label="Two athletes training together">
    <span class="text">Free First Trial Class</span>
    <span class="btn">Enroll Now</span>
  </div>

  <h2 class="section-title" style="left:27px;top:448px">Latest Blog Post</h2>
  <div class="date-box"><span class="day">26</span><span class="month">Nov</span></div>
  <article class="post-card">
    <div class="post-image" role="img" aria-label="Athlete performing a bar move on a calisthenics rig"></div>
    <div class="post-body">
      <h3 class="post-title">Temporibus autem quibusdam et aut officiis debitis</h3>
      <p class="post-date">November 10, 2015</p>
      <p class="post-text">Sed ut perspiciatis unde omnis iste natus error sit voluptatem accusantium doloremque laudantium, totam rem aperiam, eaque ipsa quae ab illo inventore veritatis et quasi architecto beatae vitae dicta sunt explicabo. Nemo enim ipsam voluptatem quia voluptas sit aspernatur aut odit aut fugit, sed quia consequuntur magni dolores eos qui ratione voluptatem sequi nesciunt. Neque porro quisquam est, qui dolorem ipsum quia dolor sit amet, consectetur, adipisci velit, sed quia non numquam eius modi tempora.</p>
    </div>
    <span class="btn">Read More</span>
  </article>

  <h2 class="section-title" style="left:729px;top:448px">Latest Blog Post</h2>
  <div class="trainer-card" style="top:494px;background:linear-gradient(135deg,#e6e6e6,#9a8a7c)" role="img" aria-label="Trainer lifting a barbell">
    <div class="info"><span class="name">Mara Lindqvist</span><span class="role">Personal Trainer</span></div>
  </div>
  <div class="trainer-card" style="top:708px;background:linear-gradient(135deg,#d8dde2,#8f8a86)" role="img" aria-label="Trainer lifting a barbell">
    <div class="info"><span class="name">Owen Harlow</span><span class="role">Weight Trainer</span></div>
  </div>

  <h2 class="section-title" style="left:729px;top:930px">Working Hours</h2>
  <table class="hours">
    <tr><td>Monday to Thursday</td><td>8am - 8pm</td></tr>
    <tr><td>Friday</td><td>8am - 6pm</td></tr>
    <tr><td>Saturday</td><td>10am - 4pm</td></tr>
    <tr><td>Sunday</td><td>12pm - 2pm</td></tr>
  </table>
</main>

<footer>
  <div class="footer-col" style="left:127px">
    <h3>Text Widget</h3>
    <p>At vero eos et accusamus et iusto odio dignissimos ducimus qui blanditiis praesentium voluptatum deleniti atque corrupti quos dolores et quas molestias excepturi sint..</p>
    <p>Nam libero tempore, cum soluta nobis est eligendi optio cumque.</p>
  </div>
  <div class="footer-col" style="left:374px">
    <h3>About Us</h3>
    <div class="about-thumb" role="img" aria-label="Gym interior"></div>
    <p>Nemo enim ipsam voluptatem quia voluptas sit aspernatur aut odit aut fugit, Neque porro quisquam est, qui dolor dolorem ipsum quia dolor sit amet, consectetur, adipisci velit.</p>
  </div>
  <div class="footer-col" style="left:623px">
    <h3>Contact Us</h3>
    <p>Sed ut perspiciatis unde omnis iste natus error sit voluptatem accusantium doloremque laudantium, totam rem aperiam.</p>
    <p>Nemo enim ipsam voluptatem quia voluptas sit aspernatur aut odit aut fugit, sed quia consequuntur magni dolores eos qui ratione.</p>
  </div>
  <div class="footer-col" style="left:872px">
    <h3>Newsletter Signup</h3>
    <div class="signup"><span class="field">Enter Your Email</span><span class="send">SEND</span></div>
    <p>Nulla at nulla justo, eget luctus tortor. Nulla facilisi. Duis aliquet egestas purus in blandit. Curabitur vulputate, ligula lacinia scelerisque tempor, lacus lacus ornare ante. Nulla at nulla justo, eget luctus tortor. Nulla facilisi. Duis aliquet egestas purus.</p>
  </div>
  <div class="footer-bottom">Summit Bodyform Gym. © 2015 <span>| Privacy Policy</span></div>
</footer>

</body>
</html>
```